Executive Business Card for Healthcare Company [Need Today]

I need a business card design for a healthcare company. The only branding the company has thus far is a logo. The cards will be utilized by company executives. The design I envision will be vibrant and appealing but with a corporate feel. They shouldn't be too casual or playful. I would like to complete this project TODAY if possible.

Target Market(s)

Healthcare vendors, other executives in healthcare and pharmaceuticals

Industry/Entity Type

Pharmaceutical

Contact Information for Business Card

See attachment

Font styles to use
Serif
Sans Serif

Colors

Designer to choose colors to be used in the design.

```html
<!DOCTYPE html>
<html lang="en">
<head>
<meta charset="utf-8">
<title>Corvane Therapeutics – Business Card</title>
<link href="https://fonts.googleapis.com/css2?family=Roboto:wght@300;400;500&display=swap" rel="stylesheet">
<style>
  :root {
    --backdrop: #3a3a3c;
    --card: #1f2022;
    --teal: #22b3be;
    --green: #3cbf86;
    --ink-light: #e6e8ea;
    --ink-muted: #b9bdc1;
    --rule: #8c9094;
    --grey-band: #6e7073;
  }
  * { box-sizing: border-box; margin: 0; padding: 0; }
  html, body { width: 799px; height: 1200px; overflow: hidden; }
  body {
    background: var(--backdrop);
    font-family: "Roboto", Arial, sans-serif;
    position: relative;
  }
  .card {
    position: absolute;
    left: 75px;
    width: 650px;
    height: 372px;
    background: var(--card);
    border-radius: 4px;
    box-shadow: 0 18px 40px rgba(0,0,0,.45);
    overflow: hidden;
  }
  .card--front { top: 105px; }
  .card--back { top: 705px; }

  .brand {
    position: absolute;
    display: flex;
    align-items: center;
  }
  .brand__mark {
    width: 86px; height: 86px;
    border: 3px solid var(--green);
    border-radius: 50%;
    flex: none;
  }
  .brand__divider {
    width: 1px; height: 62px;
    background: var(--rule);
    margin: 0 14px;
  }
  .brand__name {
    color: var(--teal);
    font-weight: 300;
    font-size: 40px;
    line-height: 1.05;
    letter-spacing: .5px;
  }
  .card--front .brand { left: 150px; top: 120px; }
  .card--back .brand { left: 40px; top: 34px; }
  .card--back .brand__mark { width: 72px; height: 72px; }
  .card--back .brand__divider { height: 52px; }
  .card--back .brand__name { font-size: 34px; }

  .website {
    position: absolute;
    left: 150px; top: 300px;
    color: var(--ink-light);
    font-size: 17px;
    letter-spacing: 3px;
  }

  .contact {
    position: absolute;
    left: 370px; top: 168px;
    color: var(--ink-light);
  }
  .contact__name {
    color: var(--teal);
    font-size: 27px;
    font-weight: 400;
    margin-left: 14px;
  }
  .contact__title {
    font-size: 13px;
    color: var(--ink-muted);
    margin: 2px 0 10px 0;
  }
  .contact__list { list-style: none; font-size: 16px; line-height: 23px; }
  .contact__list li { display: flex; align-items: center; gap: 8px; }
  .contact__list svg { width: 14px; height: 14px; flex: none; }
  .contact__address { font-size: 16px; line-height: 21px; margin-top: 2px; }

  .accent-band {
    position: absolute;
    left: 0; right: 0; bottom: 0;
    height: 14px;
    display: flex;
  }
  .accent-band__color { width: 68%; background: linear-gradient(90deg, var(--teal), var(--green)); }
  .accent-band__grey { flex: 1; background: var(--grey-band); }
</style>
</head>
<body>

<section class="card card--front" aria-label="Card front">
  <div class="brand">
    <div class="brand__mark"></div>
    <div class="brand__divider"></div>
    <div class="brand__name">Corvane<br>Therapeutics</div>
  </div>
  <div class="website">www.corvanerx.com</div>
</section>

<section class="card card--back" aria-label="Card back">
  <div class="brand">
    <div class="brand__mark"></div>
    <div class="brand__divider"></div>
    <div class="brand__name">Corvane<br>Therapeutics</div>
  </div>

  <div class="contact">
    <div class="contact__name">Daniel Marsh</div>
    <div class="contact__title">Senior Director of Marketing</div>
    <ul class="contact__list">
      <li>
        <svg viewBox="0 0 16 16" aria-hidden="true"><rect x="0" y="0" width="16" height="16" rx="3" fill="#e6e8ea"/><path d="M4.5 3.5 L6.5 3.5 L7 6 L5.8 7 C6.5 8.6 7.4 9.5 9 10.2 L10 9 L12.5 9.5 L12.5 11.5 C8 12 4 8 4.5 3.5 Z" fill="#1f2022"/></svg>
        555-210-4837
      </li>
      <li>
        <svg viewBox="0 0 16 16" aria-hidden="true"><rect x="0" y="0" width="16" height="16" rx="3" fill="#e6e8ea"/><rect x="5" y="2.5" width="6" height="11" rx="1" fill="#1f2022"/><rect x="6" y="4" width="4" height="7" fill="#e6e8ea"/></svg>
        555-310-6642
      </li>
      <li>
        <svg viewBox="0 0 16 16" aria-hidden="true"><rect x="0" y="0" width="16" height="16" rx="3" fill="#e6e8ea"/><circle cx="8" cy="8" r="5" fill="none" stroke="#1f2022" stroke-width="1.2"/><path d="M3 8 H13 M8 3 C5.5 6 5.5 10 8 13 M8 3 C10.5 6 10.5 10 8 13" fill="none" stroke="#1f2022" stroke-width="1"/></svg>
        dmarsh@corvanerx.com
      </li>
    </ul>
    <div class="contact__address">118 N Linden Avenue<br>Fairview, GA 30000</div>
  </div>

  <div class="accent-band">
    <div class="accent-band__color"></div>
    <div class="accent-band__grey"></div>
  </div>
</section>

</body>
</html>
```